QUORVIN CAPABILITY STATEMENT “Shaping Lasting Links”

QUORVIN CAPABILITY STATEMENT
“Shaping Lasting Links”
Indigenous-Owned Telecommunications & Infrastructure Solutions Partner

COVER PAGE

Visual: Modern and clean design featuring telecom towers, wind turbines, civil infrastructure, roads, and community WiFi imagery.
Tagline: “Linking Places, Lifting Futures.”
Contact:
Website: www.quorvin.com.au
Email: info@quorvin.com.au
Phone: [Insert Main Number]
“Proudly Indigenous-Owned | Compliant with Aboriginal Procurement Policy (APP) & SME Policies”
INTRODUCTION

Quorvin is a 100% Indigenous-owned leader in comprehensive infrastructure solutions, specializing in telecommunications, civil works, renewable energy, structural engineering, and site development. With over a decade of experience, we deliver safe, reliable, and culturally respectful services across Australia, from urban centers to remote wind farms and heritage sites. Our mission: “To bridge infrastructure gaps while empowering Indigenous communities and fostering sustainable growth.”

CORE CAPABILITIES

TELECOMMUNICATIONS

Tower Builds & Maintenance: Structural engineering, geotechnical analysis, foundation mapping.
Community WiFi Projects: Enhancing digital inclusion in Indigenous and remote communities.
Fiber & Wireless Networks: End-to-end installation for Velonet, Satellite, and regional connectivity.
Height Safety Systems: Design, inspection, and certification of ladder-line safety infrastructure.
CIVIL & STRUCTURAL ENGINEERING

Foundations & Concreting: Reinforced slabs, grillage, geotech-to-construction turnkey solutions.
Site Development: Earthworks, drainage, and access road/track construction.
Wind Farm Infrastructure: Reinforcing towers and integrating power systems for high-wind environments.
ROAD & ACCESS TRACK CONSTRUCTION

Construction of durable access roads and tracks: For remote projects and urban settings.
Remediation of existing tracks: Upgrading for environmental compliance and sustainability.
Facilitating logistics and site access: Particularly in challenging terrain.
POWER & ELECTRICAL SYSTEMS

Off-grid energy solutions: Solar hybrid systems, electrical structural engineering.
Grid upgrades: Ensuring compliance with AS/NZS standards and facilitating connection upgrades.
SITE REFURBISHMENT & DEMOLITION

Comprehensive refurbishment and demolition services: For outdated telecom sites and structures.
Environmentally responsible dismantling: Focused on recycling materials and minimizing land impact.
EMERGENCY RESPONSE SERVICES

24/7 Rapid Response: Over 450 callouts annually; 4,000+ emergencies resolved nationwide.
Disaster Recovery: Comprehensive support during floods, bushfires for Velonet, Marvaske, Trilumen, and regional clients.
PROJECT EXPERIENCE

Heritage Tower Upgrade

Enhanced safety and technology on culturally significant heritage sites, preserving their integrity.
Wind Farm Deployment

Delivered power, fiber, and reinforced foundations for large-scale renewable energy projects in high-wind environments.
Regional Fibre Network

Laid 200km of fiber in flood-prone regions, ensuring critical infrastructure resilience.
Indigenous Community WiFi & Connectivity

Installed sustainable WiFi networks to bridge the digital divide, supporting education, health, and business activities.
Site Demolition & Refurbishment

Safely decommissioned aging telecom sites and structures across Australia, emphasizing land reuse and environmental care.
Access Track Construction & Remediation

Developed new access roads and refurbished existing tracks to facilitate project logistics, particularly in remote or environmentally sensitive areas.
Key Stats:
+600 sites supported | 10-year Velonet partner | 98% client retention | Over 20 Indigenous community WiFi deployments

COMMITMENT TO SAFETY & QUALITY

“Pause Twice, Work Wise” Protocol: Enforced pre-task risk assessments to ensure safety at every stage.
Certifications: ISO 45001 (Safety) | ISO 9001 (Quality Management).
Safety Culture: Regular safety audits, Indigenous-led training programs, and safety initiatives focused on community well-being.
INDIGENOUS INCLUSION & COMMUNITY IMPACT

Elders Guidance Council: Provides guidance on community engagement, cultural sensitivity, and social responsibility.
Supplier Diversity: 30% procurement from Indigenous-owned businesses, fostering economic growth.
Regional Employment: 65% of our workforce originates from local communities, creating sustainable jobs.
Testimonial: “Quorvin’s partnership empowered our community with jobs and infrastructure that respects our land.” – Local Indigenous Leader

CONTACT & SERVICE AREAS

Headquarters: [Insert Address] | ABN: [Insert ABN]

24/7 Emergency Support: [Insert Dedicated Emergency Line]

Certifications & Registrations:

Trade Circle Registered, First Enterprise Register (FER)
SERVICE AREAS

National Coverage with Regional Expertise:
Major Cities: Sydney, Melbourne, Brisbane, Perth, Adelaide, Darwin, Hobart.
Regional & Remote Areas: Pilbara, Kimberley, Far North Queensland, Outback NSW.
Disaster Zones: Rapid response teams deployed nationwide for bushfire and flood incidents.
EMERGENCY SUPPORT

SLA Guarantee: 90% of emergencies addressed within 4 hours.
Partners Supported: Velonet, Marvaske, Trilumen, regional councils.
This capability statement reflects our commitment to quality, safety, and community engagement across all levels of operation, ensuring that we empower the communities we serve while maintaining the highest standards of service delivery.

Target Market(s)

Government Agencies: Especially those seeking to comply with Indigenous Procurement Policies. Telecommunication Operators: Such as Velonet, Marvaske, and Trilumen for infrastructure deployment. Indigenous Communities: Projects aimed at enhancing connectivity and digital inclusion. Utilities and Energy Providers: For power and electrical infrastructure projects. Construction and Engineering Firms: Seeking collaboration on civil and structural infrastructure projects.

Industry/Entity Type

Telecommunications and Infrastructure Development: Focused on service delivery in various contexts, including urban settings, remote locations, and Indigenous community projects. Renewable Energy: This includes wind and solar infrastructure linked to telecommunications enhancements. Civil Engineering: Related to building and maintaining essential infrastructure such as access roads and utility lines.

Font styles to use
Other font styles liked:
• Bubbleboddy neue

Requirements
Must have
• Clear demonstration of Indigenous ownership and community engagement. Compliance with relevant safety and quality certifications (e.g., ISO 45001, ISO 9001). Showcase of core capabilities in telecommunications, civil engineering, and those specific to renewable energy. Visuals that reflect the diverse range of services offered (like telecom towers and community WiFi installations).
Nice to have
• Interactive elements such as hyperlinks to project case studies or client testimonials. Infographics or visual data to highlight key statistics and project success rates. Cultural motifs or imagery that reflect Indigenous heritage and inclusion in design aspirations. QR codes that link to videos or more detailed project descriptions for digital formats.
Should not have
• Clutter or excessive text that detracts from the main messages. Generic stock images that don’t align with the specific projects or Indigenous culture. Technical jargon that could confuse stakeholders unfamiliar with industry-specific terms. Overemphasis on competitors; the focus should remain on Quorvin's unique strengths and contributions.

```html
<!DOCTYPE html>
<html lang="en">
<head>
<meta charset="utf-8">
<title>Quorvin Capability Statement</title>
<link href="https://fonts.googleapis.com/css2?family=Montserrat:wght@300;400;500;600;700;800;900&display=swap" rel="stylesheet">
<style>
  :root {
    --red: #e3262b;
    --red-deep: #b5141a;
    --ink: #1d1d1f;
    --grey-text: #6b6b6b;
    --paper: #ffffff;
    --row: #efefef;
    --navy: #2a5878;
    --teal: #2b8d87;
    --stage: #d2d2d2;
    --sky-top: #1f56c9;
    --sky-low: #5aa3e6;
  }
  * { box-sizing: border-box; margin: 0; padding: 0; }
  html, body { width: 837px; height: 1200px; overflow: hidden; }
  body {
    background: var(--stage);
    font-family: "Montserrat", Arial, sans-serif;
    color: var(--ink);
    position: relative;
  }
  .spread {
    position: absolute;
    left: 28px;
    width: 780px;
    height: 552px;
    display: flex;
    box-shadow: 0 6px 18px rgba(0,0,0,.18);
  }
  .spread--cover { top: 36px; }
  .spread--inside { top: 612px; }
  .page {
    position: relative;
    width: 390px;
    height: 552px;
    background: var(--paper);
    overflow: hidden;
  }
  .page + .page { border-left: 1px solid #e6e6e6; }
  .page svg.art { position: absolute; inset: 0; width: 100%; height: 100%; }

  /* Back cover */
  .contact { position: absolute; left: 26px; top: 44px; }
  .contact__title { font-weight: 700; font-size: 9px; margin-bottom: 8px; }
  .contact__line { display: flex; align-items: center; gap: 6px; font-size: 8.5px; font-weight: 600; margin-bottom: 6px; white-space: nowrap; }
  .contact__line svg { width: 9px; height: 9px; fill: var(--red); flex: none; }
  .compliance {
    position: absolute; left: 168px; bottom: 62px; width: 214px;
    color: #fff; font-weight: 700; font-size: 8px; line-height: 1.5;
  }

  /* Front cover */
  .brand { position: absolute; left: 40px; top: 42px; display: flex; align-items: center; gap: 8px; }
  .brand__dot { width: 22px; height: 22px; border-radius: 50%; background: var(--red); }
  .brand__name { font-weight: 300; font-size: 30px; color: var(--ink); letter-spacing: -0.5px; }
  .tagline { position: absolute; left: 40px; top: 100px; }
  .tagline__lead { color: var(--red); font-weight: 400; font-size: 15px; }
  .tagline__main { font-weight: 800; font-size: 20px; margin-top: 2px; }

  /* Inside left */
  .section-title {
    display: flex; align-items: center; gap: 6px;
    font-weight: 900; font-size: 15px; text-transform: uppercase; letter-spacing: .3px;
  }
  .section-title::before { content: ""; width: 3px; height: 16px; background: var(--red); }
  .intro { position: absolute; left: 40px; top: 40px; width: 315px; }
  .intro p { margin-top: 10px; font-size: 7.6px; line-height: 1.55; color: var(--grey-text); font-style: italic; text-align: justify; }
  .intro-photo { position: absolute; left: 50px; top: 160px; width: 290px; height: 165px; }
  .intro-photo__fill { position: absolute; inset: 0; background: linear-gradient(160deg, #9fc6e6 0%, #c9b48a 55%, #e07a2e 100%); }
  .frame-tl { position: absolute; left: -10px; top: -10px; width: 70px; height: 50px; border-top: 5px solid var(--red); border-left: 5px solid var(--red); }
  .frame-br { position: absolute; right: -10px; bottom: -10px; width: 70px; height: 50px; border-bottom: 5px solid var(--red); border-right: 5px solid var(--red); }
  .mission { position: absolute; left: 40px; top: 395px; width: 315px; }
  .mission__title { display: flex; gap: 6px; }
  .mission__title::before { content: ""; width: 3px; background: var(--red); }
  .mission__title span { display: block; font-size: 15px; line-height: 1.05; }
  .mission__light { font-weight: 300; }
  .mission__bold { font-weight: 900; }
  .mission p { margin-top: 14px; font-size: 8px; line-height: 1.6; color: var(--grey-text); font-style: italic; }

  /* Inside right */
  .capabilities { position: absolute; left: 34px; top: 36px; width: 330px; }
  .capabilities__title { display: flex; gap: 6px; margin-bottom: 14px; }
  .capabilities__title::before { content: ""; width: 3px; background: var(--red); }
  .capabilities__title span { display: block; font-size: 15px; line-height: 1.05; }
  .cap-group { margin-bottom: 12px; }
  .cap-group__head { font-weight: 900; font-size: 11px; text-transform: uppercase; margin-bottom: 5px; letter-spacing: .3px; }
  .cap-row { display: flex; align-items: center; height: 22px; margin-bottom: 3px; background: var(--row); }
  .cap-tag {
    flex: none; width: 104px; height: 100%; padding: 0 14px 0 7px;
    color: #fff; font-size: 6.8px; font-weight: 600; line-height: 1.1;
    display: flex; align-items: center;
    clip-path: polygon(0 0, 90% 0, 100% 50%, 90% 100%, 0 100%);
  }
  .cap-desc { padding-left: 8px; font-size: 6.8px; color: #333; line-height: 1.2; }
  .group--telecom .cap-group__head { color: var(--red); }
  .group--telecom .cap-tag { background: var(--red); }
  .group--civil .cap-group__head { color: var(--navy); }
  .group--civil .cap-tag { background: var(--navy); }
  .group--road .cap-group__head { color: var(--teal); }
  .group--road .cap-tag { background: var(--teal); }
</style>
</head>
<body>

<!-- Cover spread -->
<section class="spread spread--cover">
  <div class="page page--back">
    <svg class="art" viewBox="0 0 390 552" role="img" aria-label="Photo of a wind turbine beside a telecom tower on a coastal hillside under blue sky, lower half tinted red">
      <defs>
        <linearGradient id="sky" x1="0" y1="0" x2="0" y2="1">
          <stop offset="0" stop-color="var(--sky-top)"/>
          <stop offset="1" stop-color="var(--sky-low)"/>
        </linearGradient>
        <linearGradient id="tint" x1="0" y1="0" x2="0" y2="1">
          <stop offset="0" stop-color="#c0161c"/>
          <stop offset="1" stop-color="#8e0c10"/>
        </linearGradient>
        <clipPath id="photoShape">
          <path d="M150 0 H390 V552 H250 Q155 552 150 430 Z"/>
        </clipPath>
      </defs>
      <g clip-path="url(#photoShape)">
        <rect x="0" y="0" width="390" height="552" fill="url(#sky)"/>
        <path d="M0 300 Q0 290 60 292 L390 300 V552 H0 Z" fill="url(#tint)" opacity=".95"/>
      </g>
    </svg>
    <div class="contact">
      <div class="contact__title">Contact Us:</div>
      <div class="contact__line"><svg viewBox="0 0 24 24"><path d="M6.6 10.8a15 15 0 0 0 6.6 6.6l2.2-2.2a1 1 0 0 1 1-.25 11.4 11.4 0 0 0 3.6.57 1 1 0 0 1 1 1V20a1 1 0 0 1-1 1A17 17 0 0 1 3 4a1 1 0 0 1 1-1h3.5a1 1 0 0 1 1 1c0 1.25.2 2.45.57 3.57a1 1 0 0 1-.25 1z"/></svg>02-5550-0147</div>
      <div class="contact__line"><svg viewBox="0 0 24 24"><path d="M2 5h20v14H2z M2 5l10 8 10-8" /></svg>info@quorvin.com.au</div>
      <div class="contact__line"><svg viewBox="0 0 24 24"><circle cx="12" cy="12" r="10"/></svg>www.quorvin.com.au</div>
    </div>
    <p class="compliance">Proudly Indigenous-Owned | Compliant with Aboriginal Procurement Policy (APP) &amp; SME Policies</p>
  </div>

  <div class="page page--front">
    <svg class="art" viewBox="0 0 390 552" role="img" aria-label="Photo of a technician climbing a telecom tower with antennas against a pale sky">
      <defs>
        <linearGradient id="climb" x1="0" y1="0" x2="1" y2="0">
          <stop offset="0" stop-color="#ffffff"/>
          <stop offset=".45" stop-color="#e9e6e2"/>
          <stop offset="1" stop-color="#9c9690"/>
        </linearGradient>
      </defs>
      <rect x="0" y="0" width="390" height="552" fill="url(#climb)"/>
      <polygon points="0,420 390,455 390,552 0,552" fill="var(--red)"/>
    </svg>
    <div class="brand">
      <span class="brand__dot"></span>
      <span class="brand__name">Quorvin</span>
    </div>
    <div class="tagline">
      <div class="tagline__lead">Linking Places,</div>
      <div class="tagline__main">Lifting Futures.</div>
    </div>
  </div>
</section>

<!-- Inside spread -->
<section class="spread spread--inside">
  <div class="page page--intro">
    <div class="intro">
      <h2 class="section-title">Introduction</h2>
      <p>Quorvin is a 100% Indigenous-owned leader in comprehensive infrastructure solutions, specializing in telecommunications, civil works, renewable energy, structural engineering, and site development. With over a decade of experience, we deliver safe, reliable, and culturally respectful services across Australia, from urban centers to remote wind farms and heritage sites.</p>
    </div>
    <div class="intro-photo">
      <span class="frame-tl"></span>
      <div class="intro-photo__fill" role="img" aria-label="Photo of construction workers in hard hats and hi-vis vests beside scaffolding and a crane"></div>
      <span class="frame-br"></span>
    </div>
    <div class="mission">
      <h2 class="mission__title"><div><span class="mission__light">Our</span><span class="mission__bold">Mission</span></div></h2>
      <p>To bridge infrastructure gaps while empowering Indigenous communities and fostering sustainable growth.</p>
    </div>
  </div>

  <div class="page page--capabilities">
    <div class="capabilities">
      <h2 class="capabilities__title"><div><span class="mission__light">CORE</span><span class="mission__bold">CAPABILITIES</span></div></h2>

      <div class="cap-group group--telecom">
        <h3 class="cap-group__head">Telecommunications</h3>
        <div class="cap-row"><span class="cap-tag">Tower Builds &amp; Maintenance:</span><span class="cap-desc">Structural engineering, geotechnical analysis, foundation mapping.</span></div>
        <div class="cap-row"><span class="cap-tag">Community WiFi Projects:</span><span class="cap-desc">Enhancing digital inclusion in Indigenous and remote communities.</span></div>
        <div class="cap-row"><span class="cap-tag">Fiber &amp; Wireless Networks:</span><span class="cap-desc">End-to-end installation for Velonet, Satellite, and regional connectivity.</span></div>
        <div class="cap-row"><span class="cap-tag">Height Safety Systems:</span><span class="cap-desc">Design, inspection, and certification of ladder-line safety infrastructure.</span></div>
      </div>

      <div class="cap-group group--civil">
        <h3 class="cap-group__head">Civil &amp; Structural Engineering</h3>
        <div class="cap-row"><span class="cap-tag">Foundations &amp; Concreting:</span><span class="cap-desc">Reinforced slabs, grillage, geotech-to-construction turnkey solutions.</span></div>
        <div class="cap-row"><span class="cap-tag">Site Development:</span><span class="cap-desc">Earthworks, drainage, and access road/track construction.</span></div>
        <div class="cap-row"><span class="cap-tag">Wind Farm Infrastructure:</span><span class="cap-desc">Reinforcing towers and integrating power systems for high-wind environments.</span></div>
      </div>

      <div class="cap-group group--road">
        <h3 class="cap-group__head">Road &amp; Access Track Construction</h3>
        <div class="cap-row"><span class="cap-tag">Constructions Durability</span><span class="cap-desc">Construction of durable access roads and tracks - For remote projects and urban settings.</span></div>
        <div class="cap-row"><span class="cap-tag">Remediation of existing tracks:</span><span class="cap-desc">Upgrading for environmental compliance and sustainability.</span></div>
        <div class="cap-row"><span class="cap-tag">Facilitating logistics &amp; site access</span><span class="cap-desc">Particularly in challenging terrain.</span></div>
      </div>
    </div>
  </div>
</section>

</body>
</html>
```